Bright Nook Home Page (A Home Wellness e-commerce site & blog)

We need a dynamic home page created for a home wellness brand. Must be visually appealing and extremely mobile-friendly. Logos and a Navmap have been provided but that is just a guideline, PLEASE USE YOUR CREATIVITY.

Target Market(s)

1st target demo: females 24-48, 2nd target demo: all 24-48

Number of Pages Required

1 page

```html
<!DOCTYPE html>
<html lang="en">
<head>
<meta charset="UTF-8">
<title>Home | BrightNook.com</title>
<link rel="stylesheet" href="https://fonts.googleapis.com/css2?family=Lato:wght@400;700;900&display=swap">
<style>
  :root {
    --header-start: #7b62b4;
    --header-end: #2f8fd6;
    --page-bg: #ffffff;
    --backdrop: rgba(0, 0, 0, 0.46);
    --panel-bg: #ffffff;
    --divider: #e2e2e2;
    --accent: #18a0ee;
    --accent-strong: #1196e6;
    --text-muted: #6f6f6f;
    --nav-text: #ffffff;
    --fab: #2a9fd8;
  }
  * { box-sizing: border-box; margin: 0; padding: 0; }
  html, body { width: 1200px; height: 620px; overflow: hidden; }
  body {
    font-family: "Lato", sans-serif;
    background: var(--page-bg);
    position: relative;
  }
  .site-header {
    position: absolute; left: 0; top: 0; width: 1200px; height: 91px;
    background: linear-gradient(90deg, var(--header-start), var(--header-end));
    z-index: 2;
  }
  .main-nav {
    position: absolute; left: 158px; top: 0; height: 91px;
    display: flex; align-items: center; gap: 30px;
    color: var(--nav-text); font-weight: 700; font-size: 14px; letter-spacing: .3px;
  }
  .brand { font-weight: 900; font-size: 15px; }
  .social-links {
    position: absolute; left: 797px; top: 37px; display: flex; gap: 40px;
  }
  .social-dot { width: 16px; height: 16px; border-radius: 50%; background: var(--nav-text); }
  .cart-icon { position: absolute; left: 978px; top: 33px; }
  .hero-product {
    position: absolute; left: 52px; top: 95px; width: 305px; height: 340px;
    border-radius: 40% 45% 40% 50%;
    background: radial-gradient(circle at 45% 45%, #f6efe9 0%, #f0d8dc 45%, #c9d9c8 75%, rgba(255,255,255,0) 76%);
  }
  .hero-portrait {
    position: absolute; left: 790px; top: 67px; width: 344px; height: 553px;
    background: linear-gradient(180deg, #f3ece6 0%, #e7c9b4 45%, #d8a48c 100%);
    z-index: 1;
  }
  .flower-left, .flower-mid {
    position: absolute; top: 545px; width: 240px; height: 90px;
    border-radius: 50% 50% 0 0;
    background: linear-gradient(180deg, #f1d3d8, #c7dcc6);
  }
  .flower-left { left: 50px; }
  .flower-mid { left: 420px; }
  .backdrop { position: absolute; inset: 0; background: var(--backdrop); z-index: 3; }
  .chat-fab {
    position: absolute; left: 1133px; top: 545px; width: 60px; height: 60px;
    border-radius: 50%; background: var(--fab); z-index: 4;
    display: flex; align-items: center; justify-content: center;
    box-shadow: 0 0 0 4px rgba(42, 159, 216, .35);
  }
  .chat-panel {
    position: absolute; left: 395px; top: 27px; width: 394px; height: 473px;
    background: var(--panel-bg); border-radius: 3px; z-index: 5;
  }
  .chat-header {
    height: 60px; border-bottom: 1px solid var(--divider);
    display: flex; align-items: center; justify-content: flex-end; padding-right: 25px;
  }
  .hide-toggle {
    color: var(--accent); font-size: 17px; display: flex; align-items: center; gap: 7px;
  }
  .chat-log {
    height: 319px; padding: 16px 24px 0 25px; border-bottom: 1px solid var(--divider);
  }
  .message {
    color: var(--text-muted); font-weight: 700; font-size: 13px; line-height: 21.5px;
    margin-bottom: 14px;
  }
  .sender { color: var(--accent); font-weight: 900; margin-right: 3px; }
  .composer { position: relative; height: 93px; }
  .message-input {
    position: absolute; left: 50px; top: 15px; width: 129px; height: 29px;
    border: 1px solid #4a4a4a; border-radius: 2px;
    font-family: "Lato", sans-serif; font-size: 12px; color: #8a8a8a;
    padding: 6px 8px;
  }
  .send-button {
    position: absolute; left: 179px; top: 45px; width: 61px; height: 34px;
    border-radius: 17px; background: var(--accent-strong); color: #fff;
    font-weight: 700; font-size: 13px; display: flex; align-items: center; justify-content: center;
  }
</style>
</head>
<body>
  <header class="site-header">
    <nav class="main-nav">
      <span class="brand">Bright Nook</span>
      <span>HOME</span>
      <span>PROJECTS</span>
      <span>ABOUT</span>
    </nav>
    <div class="social-links">
      <span class="social-dot"></span>
      <span class="social-dot"></span>
    </div>
    <svg class="cart-icon" width="22" height="22" viewBox="0 0 24 24" aria-label="Cart">
      <path d="M2 3h3l2.6 11h11l2.4-8H6.2" fill="none" stroke="#fff" stroke-width="2.2" stroke-linejoin="round"/>
      <circle cx="9" cy="19.5" r="1.9" fill="#fff"/>
      <circle cx="17" cy="19.5" r="1.9" fill="#fff"/>
    </svg>
  </header>

  <div class="hero-product" role="img" aria-label="Glass bottle of bath salts among roses and leaves"></div>
  <div class="hero-portrait" role="img" aria-label="Woman relaxing during a head massage at a spa"></div>
  <div class="flower-left" role="img" aria-label="Pink rose with green leaves"></div>
  <div class="flower-mid" role="img" aria-label="Pink rose with green leaves"></div>

  <div class="backdrop"></div>

  <div class="chat-fab" aria-label="Open chat">
    <svg width="24" height="24" viewBox="0 0 24 24">
      <path d="M4 5h16v10H10l-5 4v-4H4z" fill="#fff"/>
    </svg>
  </div>

  <section class="chat-panel">
    <div class="chat-header">
      <span class="hide-toggle">
        <svg width="6" height="10" viewBox="0 0 6 10"><path d="M6 0v10L0 5z" fill="#f2b233"/></svg>
        Hide messages
      </span>
    </div>
    <div class="chat-log">
      <p class="message"><span class="sender">USUARIO:</span> kjflskjflksfjs fslñfksdñlfkñlsdf fs´ñlf´dsñlf´dsñlf f ´sñdflsd´fñldsf´sd fsdñflsd´ñfl</p>
      <p class="message"><span class="sender">AGENTE:</span> gdlkkgdlgñldf gdlkkgldkfgkdkgk ytrmn,trmn fdkllkgdlkgd m,yrt &nbsp;ytrolkm,,gd</p>
      <p class="message"><span class="sender">USUARIO:</span> kjflskjflksfjs fslñfksdñlfkñlsdf fs´ñlf´dsñlf´dsñlf f ´sñdflsd´fñldsf´sd fsdñflsd´ñfl</p>
      <p class="message"><span class="sender">AGENTE:</span> gdlkkgdlgñldf gdlkkgldkfgkdkgk ytrmn,trmn fdkllkgdlkgd m,yrt &nbsp;ytrolkm,,gd</p>
      <p class="message"><span class="sender">USUARIO:</span> kjflskjflksfjs fslñfksdñlfkñlsdf fs´ñlf´dsñlf´dsñlf f ´sñdflsd´fñldsf´sd fsdñflsd´ñfl</p>
    </div>
    <div class="composer">
      <div class="message-input">Write your message</div>
      <div class="send-button">SEND</div>
    </div>
  </section>
</body>
</html>
```